High Tech Real Estate Startup needs a business card

We are developing an innovative real estate marketing product based around advanced search and virtual reality.

We talk to people, we need business cards.

Target Market(s)

The target market is technology professionals and realtors.

Contact Information for Business Card

The information to be included will include

Name
Title
Phone Number
E-mail Address
www.zelquin.com

It should use simple iconography for each one of those fields.

Font styles to use
Other font styles liked:
• Co, Jubilat, Avenir

Colors

Designer to choose colors to be used in the design.

Requirements
Must have
• Clean aesthetic,
• Good use of negative space.
• It should use our company logo, shown in the attached file. It is able to use the negative of that logo (coloured font and white background) and I have attached other acceptable accent colours in a swatch file.
Should not have
• Should not be too busy
• No extraneous text (slogans, tag lines etc)

```html
<!DOCTYPE html>
<html lang="en">
<head>
<meta charset="utf-8">
<title>Zelquin Business Card</title>
<link href="https://fonts.googleapis.com/css2?family=Figtree:wght@400;500;600&display=swap" rel="stylesheet">
<style>
  :root {
    --teal: #15b7b7;
    --paper: #fbfbfb;
    --ink: #4a4a4a;
    --rule: #b4b4b4;
    --backdrop: #e6e9e9;
  }
  * { box-sizing: border-box; margin: 0; padding: 0; }
  html, body {
    width: 1200px;
    height: 1134px;
    overflow: hidden;
    background: var(--backdrop);
    font-family: "Figtree", "Helvetica Neue", Arial, sans-serif;
  }
  .card {
    position: absolute;
    left: 261px;
    width: 675px;
    height: 382px;
    box-shadow: 0 2px 6px rgba(0,0,0,0.18);
  }
  .card-front { top: 161px; background: var(--paper); }
  .card-back {
    top: 589px;
    background: var(--teal);
    display: flex;
    align-items: center;
    justify-content: center;
  }
  .logo-square {
    position: absolute;
    left: 58px;
    top: 53px;
    width: 126px;
    height: 124px;
    background: var(--teal);
    display: flex;
    align-items: center;
    justify-content: center;
    color: #fff;
    font-weight: 600;
    font-size: 20px;
    letter-spacing: 0.5px;
  }
  .holder-name {
    position: absolute;
    left: 58px;
    top: 251px;
    color: var(--teal);
    font-weight: 500;
    font-size: 30px;
    line-height: 1;
  }
  .holder-title {
    position: absolute;
    left: 59px;
    top: 287px;
    color: var(--ink);
    font-size: 19px;
    line-height: 1;
  }
  .divider {
    position: absolute;
    left: 58px;
    top: 312px;
    width: 488px;
    height: 3px;
    background: var(--rule);
  }
  .contact-row {
    position: absolute;
    left: 58px;
    top: 327px;
    display: flex;
    align-items: center;
    gap: 15px;
    color: var(--ink);
    font-size: 17px;
  }
  .contact-item { display: flex; align-items: center; gap: 9px; }
  .contact-item svg { width: 17px; height: 17px; fill: var(--teal); }
  .wordmark-large {
    color: #fff;
    font-weight: 600;
    font-size: 80px;
    letter-spacing: 2px;
    line-height: 1;
  }
</style>
</head>
<body>
  <section class="card card-front">
    <div class="logo-square">ZELQUIN</div>
    <h1 class="holder-name">Mara Delton</h1>
    <p class="holder-title">President</p>
    <div class="divider"></div>
    <div class="contact-row">
      <span class="contact-item">
        <svg viewBox="0 0 24 24" aria-hidden="true"><path d="M6.6 10.8a15.1 15.1 0 0 0 6.6 6.6l2.2-2.2c.3-.3.7-.4 1-.2 1.1.4 2.3.6 3.6.6.6 0 1 .4 1 1V20c0 .6-.4 1-1 1A17 17 0 0 1 3 4c0-.6.4-1 1-1h3.5c.6 0 1 .4 1 1 0 1.3.2 2.5.6 3.6.1.3 0 .7-.2 1z"/></svg>
        415 208 7763
      </span>
      <span class="contact-item">
        <svg viewBox="0 0 24 24" aria-hidden="true"><path d="M2 5h20v2.2l-10 6.3L2 7.2z"/><path d="M2 9.5l10 6.3 10-6.3V19H2z"/></svg>
        info@zelquin.com
      </span>
      <span class="contact-item">
        <svg viewBox="0 0 24 24" aria-hidden="true"><path d="M12 2a10 10 0 1 0 0 20 10 10 0 0 0 0-20zm6.9 6h-3a15 15 0 0 0-1.3-3.9A8 8 0 0 1 18.9 8zM12 4c.8 1.1 1.5 2.5 1.9 4h-3.8c.4-1.5 1.1-2.9 1.9-4zM4.3 14a8 8 0 0 1 0-4h3.4a16 16 0 0 0 0 4zm.8 2h3a15 15 0 0 0 1.3 3.9A8 8 0 0 1 5.1 16zm3-8h-3a8 8 0 0 1 4.3-3.9A15 15 0 0 0 8.1 8zM12 20c-.8-1.1-1.5-2.5-1.9-4h3.8c-.4 1.5-1.1 2.9-1.9 4zm2.3-6H9.7a14 14 0 0 1 0-4h4.6a14 14 0 0 1 0 4zm.3 5.9c.6-1.2 1-2.5 1.3-3.9h3a8 8 0 0 1-4.3 3.9zM16.3 14a16 16 0 0 0 0-4h3.4a8 8 0 0 1 0 4z"/></svg>
        www.zelquin.com
      </span>
    </div>
  </section>

  <section class="card card-back">
    <span class="wordmark-large">ZELQUIN</span>
  </section>
</body>
</html>
```